Quiet Harbor Prints gallery website

I need a Website for a gallery with a shopify integration or maybe even better also compatible with squarespace.
the website should have following riders: Künstler, Veranstaltungen, Shop, About Us.
some nice examples for inspiration of the website architecture are:
https://www.lindwerkraum.com/
https://www.plattenbau-salon.com/de/
https://moorlichtraum.de/
It should be easy for us to make adaptations and fill the website with new content.
Attached there is the CI an logo for the brand.
Target Market(s)
Art Collectors,
Industry/Entity Type
artgallery
Coding
Coded - Design and coding required
Number of Pages Required
3 page
Font styles to use
Look and feel

```html
<!DOCTYPE html>
<html lang="en">
<head>
<meta charset="utf-8">
<title>Quiet Harbor Prints</title>
<link rel="stylesheet" href="https://fonts.googleapis.com/css2?family=Fira+Sans:wght@500;600;700;800&family=Montserrat:wght@300;400;500;600;700&family=Noto+Serif:wght@400;700&display=swap">
<style>
:root{
  --red:#b3151f;
  --ink:#111111;
  --text:#3a3a3a;
  --muted:#8a8a8a;
  --grey-band:#f0f0f0;
  --white:#ffffff;
  --black:#000000;
}
*{margin:0;padding:0;box-sizing:border-box}
html,body{width:1200px;height:4539px;overflow:hidden}
body{position:relative;background:var(--white);font-family:"Montserrat",sans-serif;color:var(--text)}
.abs{position:absolute}
.sq{display:inline-block;width:15px;height:15px;border:2px solid var(--red);margin-left:10px;vertical-align:middle}
.section-title{position:absolute;font-family:"Fira Sans",sans-serif;font-weight:700;font-size:34px;color:var(--ink);line-height:1;white-space:nowrap}
.section-title em{font-style:normal;color:var(--red)}
.art{position:absolute}

/* top bar */
.topbar{position:absolute;left:365px;top:0;width:835px;height:44px;background:var(--black);clip-path:polygon(28px 0,100% 0,100% 100%,0 100%);color:var(--white);font-size:11px;font-weight:600}
.topbar .item{position:absolute;top:0;height:44px;display:flex;align-items:center;gap:14px}
.topbar .sep{position:absolute;top:5px;width:2px;height:32px;background:var(--white)}
.brand{position:absolute;display:flex;align-items:center;gap:10px;font-family:"Montserrat",sans-serif;font-weight:400;white-space:nowrap}
.brand .mark{width:14px;height:14px;border:2px solid var(--red)}
.nav a{position:absolute;top:72px;font-family:"Fira Sans",sans-serif;font-weight:600;font-size:16px;color:var(--ink);text-decoration:none}
.lang{position:absolute;left:869px;top:72px;width:106px;height:30px;border:1px solid #bbb;display:flex;align-items:center;justify-content:center;gap:6px;font-size:12px;font-weight:700;color:var(--ink)}
.flag{width:26px;height:14px;background:repeating-linear-gradient(#c8202f 0 2px,#fff 2px 4px);position:relative}
.flag:before{content:"";position:absolute;left:0;top:0;width:12px;height:8px;background:#2b3f8f}

/* hero */
.hero{position:absolute;left:0;top:120px;width:1200px;height:557px;background:linear-gradient(100deg,#6a1c12 0%,#c9571a 18%,#3d2f6b 38%,#2b6f8c 58%,#d2952c 78%,#4a2f75 100%)}
.hero .shade{position:absolute;inset:0;background:linear-gradient(90deg,rgba(0,0,0,.45),rgba(0,0,0,0) 55%)}
.hero h3{position:absolute;left:113px;top:201px;font-family:"Fira Sans",sans-serif;font-weight:700;font-size:20px;color:var(--white)}
.hero h1{position:absolute;left:111px;top:238px;font-family:"Fira Sans",sans-serif;font-weight:800;font-size:41px;color:var(--white);letter-spacing:.5px}
.hero p{position:absolute;left:113px;top:297px;width:430px;font-family:"Fira Sans",sans-serif;font-weight:600;font-size:13px;line-height:27px;color:var(--white)}
.btn-ghost{position:absolute;left:113px;top:361px;width:128px;height:39px;border:2px solid var(--white);color:var(--white);font-family:"Fira Sans",sans-serif;font-weight:600;font-size:13px;display:flex;align-items:center;justify-content:center}
.btn-red{position:absolute;border:3px solid var(--red);color:var(--ink);font-family:"Fira Sans",sans-serif;font-weight:600;font-size:13px;display:flex;align-items:center;justify-content:center;background:var(--white)}

/* about */
.about-text{position:absolute;left:643px;width:432px;font-size:12.5px;line-height:26px;color:var(--text)}

/* products */
.products{position:absolute;left:0;top:1270px;width:1200px;height:607px;background:var(--grey-band)}
.arrow{position:absolute;width:19px;height:19px;border-radius:50%;background:var(--red)}
.arrow svg{position:absolute;left:5px;top:4px}
.card{position:absolute;background:var(--white);box-shadow:0 2px 8px rgba(0,0,0,.12)}
.card .frame{position:absolute;border:2px solid var(--red)}
.card .frame .art{left:8px;top:8px;right:8px;bottom:8px}
.card h4{position:absolute;left:0;right:0;text-align:center;font-family:"Fira Sans",sans-serif;font-weight:700;font-size:22px;color:var(--ink)}
.card .sub{position:absolute;left:0;right:0;text-align:center;font-family:"Fira Sans",sans-serif;font-weight:500;font-size:14px;color:var(--muted)}
.card .price{position:absolute;left:0;right:0;text-align:center;font-family:"Fira Sans",sans-serif;font-weight:700;font-size:17px;color:var(--red)}
.label{position:absolute;font-family:"Fira Sans",sans-serif;font-weight:700;font-size:22px;color:var(--ink)}

/* testimonials */
.testimonials{position:absolute;left:0;top:2618px;width:1200px;height:466px;background:
  radial-gradient(ellipse 420px 200px at 15% 20%,rgba(150,205,235,.7),transparent 70%),
  radial-gradient(ellipse 500px 220px at 50% 40%,rgba(245,195,210,.6),transparent 70%),
  radial-gradient(ellipse 400px 220px at 88% 60%,rgba(160,210,240,.6),transparent 70%),
  radial-gradient(ellipse 380px 180px at 30% 80%,rgba(240,200,220,.5),transparent 70%),
  #fbf8fa}
.avatar{position:absolute;width:80px;height:80px;border-radius:50%}
.t-name{position:absolute;font-weight:700;font-size:13px;color:var(--ink)}
.stars{position:absolute;font-size:9px;color:#f2b01e;letter-spacing:1px}
.t-text{position:absolute;width:436px;font-size:12.5px;line-height:28.5px;text-align:justify;color:var(--text)}

/* projects */
.pframe{position:absolute;border:4px solid var(--ink);background:var(--white);box-shadow:0 2px 6px rgba(0,0,0,.25)}
.pframe .art{inset:10px}
.pplain{position:absolute;box-shadow:0 2px 6px rgba(0,0,0,.2)}
.pplain .art{inset:0}

/* footer */
.footer{position:absolute;left:0;top:3966px;width:1200px;height:573px;background:var(--black);color:var(--white)}
.subscribe{position:absolute;left:523px;top:113px;width:566px;height:65px;display:flex}
.subscribe .field{flex:1;background:var(--white);color:#333;font-size:14px;display:flex;align-items:center;padding-left:38px}
.subscribe .go{width:138px;background:var(--red);color:var(--white);font-weight:700;font-size:14px;display:flex;align-items:center;justify-content:center}
.f-head{position:absolute;font-weight:700;font-size:14px;letter-spacing:1px}
.f-serif{font-family:"Noto Serif",serif}
.f-link{position:absolute;font-size:13.5px;display:flex;align-items:center;gap:14px}
.f-contact{position:absolute;display:flex;align-items:center;gap:22px;font-family:"Noto Serif",serif;font-size:13px}
.f-contact .ico{width:28px;height:28px;border-radius:5px;background:var(--white);display:flex;align-items:center;justify-content:center}
.social{position:absolute;top:349px;width:20px;height:20px;border:2px solid var(--white);border-radius:2px}
.f-rule{position:absolute;left:113px;top:513px;width:978px;height:1px;background:#777}
.copy{position:absolute;left:0;right:0;top:532px;text-align:center;font-family:"Noto Serif",serif;font-size:12px}
</style>
</head>
<body>

<!-- header -->
<div class="brand" style="left:114px;top:64px;font-size:16px;color:var(--ink)">Quiet Harbor Prints<span class="mark"></span></div>

<div class="topbar">
  <div class="item" style="left:53px">
    <svg width="16" height="20" viewBox="0 0 16 20"><path d="M8 0a7 7 0 0 0-7 7c0 5 7 13 7 13s7-8 7-13a7 7 0 0 0-7-7z" fill="#fff"/><circle cx="8" cy="7" r="2.6" fill="#000"/></svg>
    <span>Lorem Ipsum,Usa-437916</span>
  </div>
  <div class="sep" style="left:282px"></div>
  <div class="item" style="left:315px">
    <svg width="20" height="20" viewBox="0 0 24 24"><path d="M6.6 10.8a15 15 0 0 0 6.6 6.6l2.2-2.2c.3-.3.7-.4 1-.2 1.1.4 2.3.6 3.6.6.6 0 1 .4 1 1V20c0 .6-.4 1-1 1A17 17 0 0 1 3 4c0-.6.4-1 1-1h3.5c.6 0 1 .4 1 1 0 1.3.2 2.5.6 3.6.1.3 0 .7-.2 1z" fill="#fff"/></svg>
    <span>+1 888 888 8888</span>
  </div>
  <div class="sep" style="left:486px"></div>
  <div class="item" style="left:536px">
    <svg width="22" height="16" viewBox="0 0 22 16"><rect width="22" height="16" fill="#fff"/><path d="M0 0l11 9 11-9M0 16l8-8M22 16l-8-8" stroke="#000" stroke-width="1.6" fill="none"/></svg>
    <span>info@quietharborprints.com</span>
  </div>
</div>

<nav class="nav">
  <a style="left:449px">Artists</a>
  <a style="left:555px">Events</a>
  <a style="left:657px">Shop</a>
  <a style="left:744px">About Us</a>
</nav>
<div class="lang"><span class="flag"></span>Eng
  <svg width="10" height="6" viewBox="0 0 10 6"><path d="M1 1l4 4 4-4" stroke="#111" stroke-width="1.3" fill="none"/></svg>
</div>
<svg class="abs" style="left:1000px;top:75px" width="86" height="22" viewBox="0 0 86 22" fill="none" stroke="#333" stroke-width="1.6">
  <circle cx="9" cy="6" r="4.5"/><path d="M1 19c1-5 4-7 8-7s7 2 8 7"/>
  <circle cx="40" cy="8" r="6"/><path d="M44.5 12.5l6 6"/>
  <path d="M75 20l-7-7a4.5 4.5 0 0 1 7-5.5 4.5 4.5 0 0 1 7 5.5z"/>
</svg>

<!-- hero -->
<section class="hero">
  <div class="art" role="img" aria-label="Colourful cubist painting of a woman's face" style="inset:0"></div>
  <div class="shade"></div>
  <h3>Welcome To</h3>
  <h1>QUIET HARBOR PRINTS</h1>
  <p>Lorem ipsum dolor sit amet, consectetur adipiscing elit, sed do eiusmod tempor incididunt ut labore et dolore magna aliqua.</p>
  <div class="btn-ghost">Get Started</div>
</section>

<!-- about -->
<section class="about">
  <div class="art" role="img" aria-label="Painter working at an easel beside a painting of a robot figure" style="left:111px;top:766px;width:303px;height:318px;background:linear-gradient(110deg,#5b3b2a,#b58a5e 45%,#7f98a8 70%,#c79b3c)"></div>
  <div class="abs" style="left:414px;top:874px;width:49px;height:76px;border-top:3px solid var(--red);border-right:3px solid var(--red)"></div>
  <div class="abs" style="left:168px;top:1084px;width:48px;height:36px;border-left:3px solid var(--ink);border-bottom:3px solid var(--ink)"></div>
  <div class="abs" style="left:214px;top:948px;width:345px;height:227px;border-top:4px solid var(--ink);border-left:4px solid var(--ink)"></div>
  <div class="art" role="img" aria-label="Gallery hall with framed colourful paintings on dark walls" style="left:224px;top:957px;width:335px;height:218px;background:linear-gradient(180deg,#1d2d33,#2c5566 55%,#12222a)"></div>

  <div class="section-title" style="left:643px;top:766px">About <em>Us</em><span class="sq"></span></div>
  <p class="about-text" style="top:826px">Lorem ipsum dolor sit amet, consectetur adipiscing elit, sed do eiusmod tempor incididunt ut labore et dolore magna aliqua. Ut enim ad minim veniam, quis nostrud exercitation ullamco laboris nisi ut aliquip ex ea commodo consequat.</p>
  <p class="about-text" style="top:939px">Duis aute irure dolor in reprehenderit in voluptate velit esse cillum dolore eu fugiat nulla pariatur. Excepteur sint occaecat cupidatat non proident, sunt in culpa qui officia deserunt mollit anim id est laborum.</p>
  <div class="btn-red" style="left:641px;top:1073px;width:129px;height:41px">Get Started</div>
</section>

<!-- products -->
<section class="products">
  <div class="section-title" style="left:113px;top:60px">Our <em>Products</em><span class="sq"></span></div>
  <div class="arrow" style="left:1036px;top:63px"><svg width="9" height="11" viewBox="0 0 9 11"><path d="M6 1L2 5.5 6 10" stroke="#fff" stroke-width="2" fill="none"/></svg></div>
  <div class="arrow" style="left:1066px;top:63px"><svg width="9" height="11" viewBox="0 0 9 11"><path d="M3 1l4 4.5L3 10" stroke="#fff" stroke-width="2" fill="none"/></svg></div>

  <div class="card" style="left:113px;top:140px;width:280px;height:393px">
    <div class="frame" style="left:32px;top:22px;width:217px;height:235px"><div class="art" role="img" aria-label="Abstract sunset landscape print in peach and teal" style="background:linear-gradient(180deg,#e6d9c6,#d99a74 50%,#3f6670)"></div></div>
    <h4 style="top:278px">Sunset</h4><div class="sub" style="top:316px">Lorem Ipsum</div><div class="price" style="top:342px">$50.00</div>
  </div>
  <div class="card" style="left:407px;top:140px;width:280px;height:393px">
    <div class="frame" style="left:32px;top:22px;width:217px;height:235px"><div class="art" role="img" aria-label="Textured green leaf on dark teal background" style="background:linear-gradient(160deg,#2b4650,#51705f 50%,#263c45)"></div></div>
    <h4 style="top:278px">Leaf</h4><div class="sub" style="top:316px">Lorem Ipsum</div><div class="price" style="top:342px">$50.00</div>
  </div>
  <div class="card" style="left:700px;top:140px;width:280px;height:393px">
    <div class="frame" style="left:32px;top:22px;width:217px;height:235px"><div class="art" role="img" aria-label="Abstract plants in orange and cream on grey" style="background:linear-gradient(180deg,#5d6466,#9c8a78 55%,#3a4f55)"></div></div>
    <h4 style="top:278px">Dessart</h4><div class="sub" style="top:316px">Lorem Ipsum</div><div class="price" style="top:342px">$50.00</div>
  </div>
  <div class="card" style="left:992px;top:140px;width:280px;height:393px">
    <div class="frame" style="left:32px;top:22px;width:217px;height:235px"><div class="art" role="img" aria-label="Black and white ink portrait" style="background:linear-gradient(135deg,#1a1a1a,#6a6a6a)"></div></div>
    <h4 style="top:278px;left:-8px">People</h4><div class="sub" style="top:316px;left:-8px">Lorem Ipsum</div><div class="price" style="top:342px;left:-8px">$50.00</div>
  </div>
</section>

<!-- new arrivals -->
<section class="arrivals">
  <div class="section-title" style="left:113px;top:1974px">New <em>Arrivals</em><span class="sq"></span></div>
  <div class="arrow" style="left:1036px;top:1979px"><svg width="9" height="11" viewBox="0 0 9 11"><path d="M6 1L2 5.5 6 10" stroke="#fff" stroke-width="2" fill="none"/></svg></div>
  <div class="arrow" style="left:1066px;top:1979px"><svg width="9" height="11" viewBox="0 0 9 11"><path d="M3 1l4 4.5L3 10" stroke="#fff" stroke-width="2" fill="none"/></svg></div>

  <div class="card" style="left:-20px;top:2076px;width:231px;height:394px">
    <div class="art" role="img" aria-label="Painting of pink and red flowers" style="left:20px;top:21px;width:174px;height:361px;background:linear-gradient(160deg,#e8906e,#c9507a 55%,#7a4a8a)"></div>
  </div>
  <div class="card" style="left:229px;top:2076px;width:280px;height:394px">
    <div class="frame" style="left:23px;top:31px;width:229px;height:229px"><div class="art" role="img" aria-label="Cubist painting of an embracing couple" style="background:linear-gradient(135deg,#2e2a2c,#8a6e5a 55%,#3d3535)"></div></div>
    <h4 style="top:271px">Wedding</h4><div class="sub" style="top:310px">Lorem Ipsum</div><div class="price" style="top:340px">$1500.00</div>
  </div>
  <div class="card" style="left:516px;top:2076px;width:279px;height:394px">
    <div class="art" role="img" aria-label="Abstract fluid painting in teal, red and orange" style="left:21px;top:21px;width:237px;height:352px;background:linear-gradient(170deg,#2a7c88,#b8503a 55%,#d9852e)"></div>
  </div>
  <div class="card" style="left:803px;top:2076px;width:279px;height:394px">
    <div class="art" role="img" aria-label="Textured abstract painting in orange and turquoise" style="left:22px;top:18px;width:237px;height:360px;background:linear-gradient(170deg,#2a8db0,#d9742e 50%,#1f5d80)"></div>
  </div>
  <div class="label" style="left:26px;top:2492px">Flowers</div>
  <div class="label" style="left:610px;top:2492px">Messy</div>
  <div class="label" style="left:897px;top:2492px">Paint</div>
</section>

<!-- testimonials -->
<section class="testimonials">
  <div class="section-title" style="left:0;right:0;top:65px;text-align:center">What Our <em>Client Says?</em><span class="sq"></span></div>
  <div class="arrow" style="left:35px;top:287px"><svg width="9" height="11" viewBox="0 0 9 11"><path d="M6 1L2 5.5 6 10" stroke="#fff" stroke-width="2" fill="none"/></svg></div>
  <div class="arrow" style="left:1145px;top:279px"><svg width="9" height="11" viewBox="0 0 9 11"><path d="M3 1l4 4.5L3 10" stroke="#fff" stroke-width="2" fill="none"/></svg></div>

  <div class="avatar" role="img" aria-label="Client portrait" style="left:116px;top:175px;background:linear-gradient(135deg,#a88068,#5a4436)"></div>
  <div class="t-name" style="left:217px;top:192px">ANDREW</div>
  <div class="stars" style="left:217px;top:210px">★★★★★</div>
  <p class="t-text" style="left:116px;top:268px">Lorem ipsum dolor sit amet, consectetur adipiscing elit, sed do eiusmod tempor incididunt ut labore et dolore magna aliqua. Ut enim ad minim veniam, quis nostrud exercitation ullamco laboris nisi ut aliquip ex ea commodo consequat.</p>

  <div class="abs" style="left:598px;top:254px;width:3px;height:118px;background:#cfcfcf"></div>

  <div class="avatar" role="img" aria-label="Client portrait" style="left:642px;top:175px;background:linear-gradient(135deg,#7a5038,#2a1a12)"></div>
  <div class="t-name" style="left:742px;top:192px">JESSYKA</div>
  <div class="stars" style="left:742px;top:210px">★★★★★</div>
  <p class="t-text" style="left:641px;top:268px">Lorem ipsum dolor sit amet, consectetur adipiscing elit, sed do eiusmod tempor incididunt ut labore et dolore magna aliqua. Ut enim ad minim veniam, quis nostrud exercitation ullamco laboris nisi ut aliquip ex ea commodo consequat.</p>
</section>

<!-- recent projects -->
<section class="projects">
  <div class="section-title" style="left:0;right:0;top:3171px;text-align:center">Recent <em>Projects</em><span class="sq"></span></div>

  <div class="pframe" style="left:95px;top:3281px;width:153px;height:208px"><div class="art" role="img" aria-label="City street painting with reflections" style="background:linear-gradient(180deg,#3e6ea8,#7a6a78 55%,#24324e)"></div></div>
  <div class="pplain" style="left:277px;top:3263px;width:176px;height:122px"><div class="art" role="img" aria-label="Teal abstract print on beige" style="background:linear-gradient(135deg,#ddd6c8,#8fa8a4)"></div></div>
  <div class="pframe" style="left:477px;top:3272px;width:149px;height:210px"><div class="art" role="img" aria-label="Pink flowers botanical print" style="background:linear-gradient(180deg,#b8b8a2,#c98a96)"></div></div>
  <div class="pplain" style="left:655px;top:3263px;width:156px;height:205px"><div class="art" role="img" aria-label="Cubist blue portrait" style="background:linear-gradient(135deg,#1f3f7a,#6f8fb8)"></div></div>
  <div class="pplain" style="left:835px;top:3323px;width:229px;height:127px"><div class="art" role="img" aria-label="Still life with jugs and fruit" style="background:linear-gradient(180deg,#3b3a33,#8a7b62)"></div></div>

  <div class="pframe" style="left:93px;top:3513px;width:148px;height:205px"><div class="art" role="img" aria-label="Botanical stem print on pink" style="background:linear-gradient(180deg,#e2cdd2,#c4a0aa)"></div></div>
  <div class="pframe" style="left:278px;top:3404px;width:168px;height:233px"><div class="art" role="img" aria-label="Purple flowers botanical print" style="background:linear-gradient(180deg,#a596c4,#a6ae8e)"></div></div>
  <div class="pframe" style="left:479px;top:3506px;width:141px;height:194px"><div class="art" role="img" aria-label="Single-line face drawing" style="background:#f2f2f0"></div></div>
  <div class="pplain" style="left:647px;top:3489px;width:181px;height:271px"><div class="art" role="img" aria-label="Boho abstract print in teal and sand" style="background:linear-gradient(180deg,#335e68,#c8a68a 60%,#e6dccd)"></div></div>
  <div class="pplain" style="left:851px;top:3482px;width:261px;height:146px"><div class="art" role="img" aria-label="Bright colourful flower bouquet painting" style="background:linear-gradient(120deg,#e8a838,#d8507a 50%,#4a9ec0)"></div></div>

  <div class="pplain" style="left:277px;top:3665px;width:169px;height:115px"><div class="art" role="img" aria-label="Abstract print in teal and orange" style="background:linear-gradient(120deg,#4a7078,#c8906a)"></div></div>
  <div class="art" role="img" aria-label="Watercolour camera painting" style="left:863px;top:3656px;width:134px;height:141px;background:linear-gradient(135deg,#e9b0a0,#5a5a6a 50%,#8ac0dc)"></div>

  <div class="btn-red" style="left:534px;top:3829px;width:130px;height:40px">View All</div>
</section>

<!-- footer -->
<footer class="footer">
  <div class="brand" style="left:116px;top:108px;font-size:22px;color:var(--white)">Quiet Harbor Prints<span class="mark"></span></div>

  <div class="subscribe"><div class="field">Enter Email Address</div><div class="go">Subscribe</div></div>

  <div class="f-head" style="left:125px;top:306px">Quick Links</div>
  <div class="f-link" style="left:118px;top:344px"><svg width="12" height="10" viewBox="0 0 12 10"><path d="M1 1l4 4-4 4M6 1l4 4-4 4" stroke="#fff" stroke-width="1.4" fill="none"/></svg>Artists</div>
  <div class="f-link" style="left:118px;top:381px"><svg width="12" height="10" viewBox="0 0 12 10"><path d="M1 1l4 4-4 4M6 1l4 4-4 4" stroke="#fff" stroke-width="1.4" fill="none"/></svg>Events</div>
  <div class="f-link" style="left:118px;top:416px"><svg width="12" height="10" viewBox="0 0 12 10"><path d="M1 1l4 4-4 4M6 1l4 4-4 4" stroke="#fff" stroke-width="1.4" fill="none"/></svg>Shop</div>
  <div class="f-link" style="left:118px;top:453px"><svg width="12" height="10" viewBox="0 0 12 10"><path d="M1 1l4 4-4 4M6 1l4 4-4 4" stroke="#fff" stroke-width="1.4" fill="none"/></svg>About Us</div>

  <div class="f-head" style="left:359px;top:306px">Help Links</div>
  <div class="f-link" style="left:358px;top:344px"><svg width="12" height="10" viewBox="0 0 12 10"><path d="M1 1l4 4-4 4M6 1l4 4-4 4" stroke="#fff" stroke-width="1.4" fill="none"/></svg>Privacy Policy</div>
  <div class="f-link" style="left:358px;top:381px"><svg width="12" height="10" viewBox="0 0 12 10"><path d="M1 1l4 4-4 4M6 1l4 4-4 4" stroke="#fff" stroke-width="1.4" fill="none"/></svg>Terms &amp; Conditions</div>
  <div class="f-link" style="left:358px;top:416px"><svg width="12" height="10" viewBox="0 0 12 10"><path d="M1 1l4 4-4 4M6 1l4 4-4 4" stroke="#fff" stroke-width="1.4" fill="none"/></svg>Disclaimer</div>

  <div class="f-head f-serif" style="left:604px;top:297px">Contact Details</div>
  <div class="f-contact" style="left:608px;top:335px"><span class="ico"><svg width="12" height="16" viewBox="0 0 16 20"><path d="M8 0a7 7 0 0 0-7 7c0 5 7 13 7 13s7-8 7-13a7 7 0 0 0-7-7z" fill="#000"/><circle cx="8" cy="7" r="2.6" fill="#fff"/></svg></span>Lorem Ipsum,Usa -437916</div>
  <div class="f-contact" style="left:608px;top:391px"><span class="ico"><svg width="16" height="16" viewBox="0 0 24 24"><path d="M6.6 10.8a15 15 0 0 0 6.6 6.6l2.2-2.2c.3-.3.7-.4 1-.2 1.1.4 2.3.6 3.6.6.6 0 1 .4 1 1V20c0 .6-.4 1-1 1A17 17 0 0 1 3 4c0-.6.4-1 1-1h3.5c.6 0 1 .4 1 1 0 1.3.2 2.5.6 3.6.1.3 0 .7-.2 1z" fill="#000"/></svg></span>+1 888 888 8888</div>
  <div class="f-contact" style="left:608px;top:441px"><span class="ico"><svg width="16" height="12" viewBox="0 0 22 16"><rect width="22" height="16" fill="#000"/><path d="M0 0l11 9 11-9" stroke="#fff" stroke-width="1.6" fill="none"/></svg></span>info@quietharborprints.com</div>

  <div class="f-head f-serif" style="left:943px;top:303px">Follow Us</div>
  <div class="social" style="left:944px"></div>
  <div class="social" style="left:978px"></div>
  <div class="social" style="left:1009px"></div>
  <div class="social" style="left:1041px"></div>

  <div class="f-rule"></div>
  <div class="copy">Copyright © 2024 Quiet Harbor Prints. All rights reserved.</div>
</footer>

</body>
</html>
```